Business Card for a New Zealand IT Startup

I need a business card for VELTA Holdings. We are a young startup based in New Zealand working in internet marketing and web development. The design should have some element connected to New Zealand, such as wave, koru or silver fern, just don't use a kiwi bird.

```html
<!DOCTYPE html>
<html lang="en">
<head>
<meta charset="utf-8">
<title>VELTA Holdings — Business Card</title>
<link href="https://fonts.googleapis.com/css2?family=Montserrat:wght@500;700&family=Open+Sans:wght@400;600&display=swap" rel="stylesheet">
<style>
  :root {
    --backdrop: #e4e4e4;
    --card: #fbfbfb;
    --brand-blue: #1b6db5;
    --brand-blue-light: #4a9ad8;
    --brand-orange: #e8551f;
    --ink: #3c3c3c;
    --ink-soft: #6a6a6a;
  }
  * { box-sizing: border-box; margin: 0; padding: 0; }
  html, body { width: 1200px; height: 852px; overflow: hidden; }
  body {
    background: var(--backdrop);
    font-family: "Open Sans", sans-serif;
    color: var(--ink);
    position: relative;
  }
  .card {
    position: absolute;
    width: 520px;
    height: 300px;
    background: var(--card);
    border-radius: 22px;
    box-shadow: 0 8px 22px rgba(0,0,0,0.18);
  }
  .card--front { left: 50px; top: 110px; }
  .card--back { left: 630px; top: 440px; }

  .wordmark {
    display: flex;
    align-items: center;
    gap: 14px;
    font-family: "Montserrat", sans-serif;
    font-weight: 700;
    color: var(--brand-blue);
    white-space: nowrap;
  }
  /* Koru / wave emblem area: plain circle holding the NZ wave mark */
  .wordmark__emblem {
    border-radius: 50%;
    background: radial-gradient(circle at 35% 35%, var(--brand-blue-light), var(--brand-blue));
    flex: none;
  }

  .card--front .wordmark {
    position: absolute;
    left: 0; right: 0; top: 92px;
    justify-content: center;
    font-size: 40px;
  }
  .card--front .wordmark__emblem { width: 52px; height: 52px; }

  .front-url {
    position: absolute;
    left: 0; right: 0; top: 218px;
    display: flex;
    align-items: center;
    justify-content: center;
    gap: 14px;
    font-size: 15px;
    color: var(--ink);
  }
  .front-url__rule { width: 90px; height: 2px; background: var(--brand-blue); }
  .front-url b { font-weight: 600; color: var(--brand-orange); }

  .card--back .wordmark {
    position: absolute;
    left: 0; right: 0; top: 36px;
    justify-content: center;
    font-size: 30px;
  }
  .card--back .wordmark__emblem { width: 40px; height: 40px; }

  .rule { position: absolute; height: 2px; }
  .rule--blue { background: var(--brand-blue); left: 250px; right: 26px; top: 140px; }
  .rule--orange { background: var(--brand-orange); left: 26px; right: 210px; top: 262px; }

  .contact-list {
    position: absolute;
    left: 270px; top: 150px;
    list-style: none;
    font-size: 13.5px;
    line-height: 22px;
  }
  .contact-list li { display: flex; align-items: center; gap: 10px; }
  .contact-list svg { width: 13px; height: 13px; fill: var(--brand-orange); flex: none; }

  .person {
    position: absolute;
    left: 40px; top: 160px;
    text-align: right;
    width: 210px;
  }
  .person__name {
    font-family: "Montserrat", sans-serif;
    font-weight: 700;
    font-size: 21px;
    color: var(--brand-blue);
  }
  .person__role { font-size: 13px; color: var(--ink-soft); }

  .address {
    position: absolute;
    left: 40px; right: 26px; top: 226px;
    font-size: 14px;
    color: var(--ink);
  }
</style>
</head>
<body>

  <section class="card card--front" aria-label="Card front">
    <div class="wordmark">
      <span class="wordmark__emblem" role="img" aria-label="New Zealand koru wave emblem"></span>
      VELTA Holdings
    </div>
    <div class="front-url">
      <span class="front-url__rule"></span>
      <span>www.<b>velta</b>holdings.com</span>
      <span class="front-url__rule"></span>
    </div>
  </section>

  <section class="card card--back" aria-label="Card back">
    <div class="wordmark">
      <span class="wordmark__emblem" role="img" aria-label="New Zealand koru wave emblem"></span>
      VELTA Holdings
    </div>
    <div class="rule rule--blue"></div>

    <div class="person">
      <p class="person__name">Mara Ellison</p>
      <p class="person__role">Managing Director</p>
    </div>

    <ul class="contact-list">
      <li>
        <svg viewBox="0 0 24 24" aria-hidden="true"><path d="M6.6 10.8a15.1 15.1 0 0 0 6.6 6.6l2.2-2.2a1 1 0 0 1 1-.25 11.4 11.4 0 0 0 3.6.57 1 1 0 0 1 1 1V20a1 1 0 0 1-1 1A17 17 0 0 1 3 4a1 1 0 0 1 1-1h3.5a1 1 0 0 1 1 1c0 1.25.2 2.45.57 3.57a1 1 0 0 1-.25 1z"/></svg>
        888-4210-553
      </li>
      <li>
        <svg viewBox="0 0 24 24" aria-hidden="true"><path d="M2 5h20v14H2z M2 5l10 8 10-8" stroke="#fbfbfb" stroke-width="1.6"/></svg>
        hello@veltaholdings.com
      </li>
      <li>
        <svg viewBox="0 0 24 24" aria-hidden="true"><circle cx="12" cy="12" r="10"/><path d="M2 12h20M12 2c3 3 3 17 0 20M12 2c-3 3-3 17 0 20" stroke="#fbfbfb" stroke-width="1.4" fill="none"/></svg>
        www.veltaholdings.com
      </li>
    </ul>

    <p class="address">18 Harbour Lane, Wellington, NZ 6011</p>
    <div class="rule rule--orange"></div>
  </section>

</body>
</html>
```